Drabek Partners envision a corporate 22 year old theme with as many features functional

We need an interactive website designed.
Fully interactive with social media
Fully Interactive with Live content
you should map out how you'd like the website to work. This is important both for user experience and for SEO, since Zorvia considers the content and structure of a site when it ranks
Crucial Business Information
Keep text to a minimum when it comes to your mission statement, because you should be writing things so people can skim — we all have short attention spans.
Depending on your business, you should have a few things on your website that fall into the realm of "information." Tailor your site so that it offers the information users are likely to be looking for.
Content
Clear Navigation
Security
Social Media Intergration
Mobile Ready
Feel free to forgo these things on your website:
Music
Flash
Anything that autoplays,
Extraneous information and media
Industry/Entity Type
Media
Contact Information for Business Card
Coding
Coded - Design and coding required
Number of Pages Required
1 page
Other font styles liked:
- as per uploaded Guidelines
Requirements
Must have
Nice to have
Should not have

```html
<!DOCTYPE html>
<html lang="en">
<head>
<meta charset="utf-8">
<title>Drabek Partners</title>
<link href="https://fonts.googleapis.com/css2?family=Exo+2:wght@300;400;500;600;700&family=Open+Sans:wght@400;600;700&display=swap" rel="stylesheet">
<style>
:root{
  --green:#1fb883;
  --green-dark:#12946a;
  --red:#d8232a;
  --ink:#2a2a2a;
  --body:#555;
  --charcoal:#2d2d2d;
  --tab:#3a3a3a;
  --grey-band:#f1f1f1;
  --line:#cfcfcf;
  --white:#fff;
}
*{box-sizing:border-box;margin:0;padding:0}
html,body{width:1200px;height:3564px;overflow:hidden;background:var(--white)}
body{font-family:"Open Sans",Arial,sans-serif;color:var(--body);position:relative}
.page{position:relative;width:1200px;height:3564px}
section,header,footer{position:absolute;left:0;width:1200px}

/* header + hero */
.site-header{top:0;height:660px;background:#000}
.hero-visual{position:absolute;inset:0;background:
  radial-gradient(ellipse 900px 260px at 50% 115%,#5c86b8 0%,#2b4c78 35%,rgba(10,20,40,0) 70%),
  linear-gradient(180deg,#000 0%,#05070c 55%,#10203a 100%)}
.logo-tab{position:absolute;left:48px;top:0;width:270px;height:128px;background:var(--tab);border-radius:0 0 40px 40px;display:flex;align-items:center;justify-content:center}
.wordmark{font-family:"Exo 2",sans-serif;font-weight:700;color:var(--white);font-size:30px;line-height:1.05;text-align:center}
.main-nav{position:absolute;right:10px;top:62px;display:flex;gap:20px;list-style:none}
.main-nav li{font-family:"Exo 2",sans-serif;font-weight:500;font-size:14px;color:#e6e6e6;text-transform:uppercase;position:relative}
.main-nav li.is-active{color:var(--green)}
.main-nav li.is-active::before{content:"";position:absolute;left:50%;top:-26px;width:14px;height:14px;border:3px solid var(--green);border-radius:50%;transform:translateX(-50%)}
.hero-tagline{position:absolute;top:360px;left:0;width:1200px;text-align:center;font-family:"Exo 2",sans-serif;font-weight:300;font-size:52px;color:var(--white);letter-spacing:1px}
.hero-tagline .sep{display:inline-block;width:14px;height:14px;border:3px solid var(--green);border-radius:50%;margin:0 12px;vertical-align:middle}

/* section titles */
.section-title{position:absolute;left:0;width:1200px;display:flex;align-items:center;justify-content:center;gap:18px;font-family:"Exo 2",sans-serif;font-weight:600;font-size:31px;color:var(--ink)}
.section-title::before,.section-title::after{content:"";width:150px;height:1px;background:var(--line)}
.section-title .mark{width:16px;height:16px;border:3px solid var(--green);border-radius:50%}
.section-title em{font-style:normal;color:var(--green)}
.section-title.on-green{color:var(--white)}
.section-title.on-green::before,.section-title.on-green::after{background:rgba(255,255,255,.6)}
.section-title.on-green .mark{border-color:var(--white)}

.btn{position:absolute;left:505px;width:190px;height:44px;border-radius:8px;background:var(--green);color:var(--white);font-family:"Exo 2",sans-serif;font-weight:600;font-size:17px;display:flex;align-items:center;justify-content:center;box-shadow:0 6px 8px -4px rgba(0,0,0,.3)}

/* who we are */
.who{top:660px;height:630px;background:var(--white);box-shadow:inset 0 14px 14px -12px rgba(0,0,0,.18)}
.who .section-title{top:60px}
.who-grid{position:absolute;top:128px;left:54px;width:1100px;display:grid;grid-template-columns:1fr 1fr 1fr}
.who-card{padding:0 38px}
.who-card:first-child{padding-left:0}
.who-card:last-child{padding-right:0}
.who-card+.who-card{border-left:1px solid var(--line)}
.who-visual{height:185px;margin-bottom:30px}
.v-directors{background:linear-gradient(135deg,#f5f5f5,#c9c9c9 60%,#8fb8e0)}
.v-motivators{background:linear-gradient(180deg,#ffffff 0%,#e8e8e8 45%,#8cc6ef 100%)}
.v-energisers{background:linear-gradient(135deg,#3f6a3c,#2f5530 60%,#506e46)}
.who-card h3{font-weight:700;font-size:20px;color:var(--ink);margin-bottom:12px}
.who-card p{font-size:14.5px;line-height:1.45}
.who .btn{top:518px}

/* what we do */
.do{top:1290px;height:537px;background:var(--grey-band)}
.do .section-title{top:60px}
.do-grid{position:absolute;top:135px;left:52px;width:1110px;display:grid;grid-template-columns:1fr 1fr 1fr}
.do-col{padding:0 24px}
.do-col:first-child{padding-left:0}
.do-col:last-child{padding-right:0}
.do-col+.do-col{border-left:1px solid var(--line)}
.do-col h3{font-weight:700;font-size:17px;color:var(--ink);margin-bottom:18px;white-space:nowrap}
.do-col h3 em{font-style:normal;color:var(--red)}
.do-list{list-style:none}
.do-list li{position:relative;padding-left:26px;font-size:14px;line-height:1.4;margin-bottom:14px}
.do-list li::before{content:"";position:absolute;left:0;top:4px;width:9px;height:9px;border:2.5px solid var(--green);border-radius:50%}
.do .btn{top:446px}

/* what makes us different */
.diff{top:1827px;height:503px;background:radial-gradient(ellipse at 50% 45%,#2cc08e 0%,#1a9f74 55%,#118461 100%)}
.diff .section-title{top:68px}
.diff-art{position:absolute;left:0;top:0}
.diff-hub{position:absolute;left:505px;top:180px;width:190px;height:190px;border-radius:50%;background:#111;border:6px solid #fff;display:flex;align-items:center;justify-content:center}
.diff-hub .wordmark{font-size:28px}
.trait{position:absolute;width:330px;color:var(--white);font-size:15px;line-height:1.35}
.trait strong{font-family:"Exo 2",sans-serif;font-weight:700;font-size:18px;text-transform:uppercase}
.trait .tag{font-size:14px}
.trait.left{text-align:right}
.t-responsive{left:20px;top:150px}
.t-transparent{left:842px;top:160px}
.t-supportive{left:20px;top:336px}
.t-performance{left:842px;top:348px}

/* our group */
.group{top:2330px;height:760px;background:var(--white)}
.group .section-title{top:60px}
.org-lines{position:absolute;left:0;top:0}
.org-top{position:absolute;left:473px;top:132px;width:262px;height:130px;background:#555;color:var(--white);text-align:center;box-shadow:0 5px 10px rgba(0,0,0,.25);padding-top:14px}
.org-top h4{font-weight:600;font-size:17px;margin-bottom:8px}
.org-top p{font-size:16px;line-height:1.3}
.org-side{position:absolute;left:950px;top:162px;width:180px;height:43px;background:#9b9b9b;color:var(--white);font-size:14px;font-weight:600;display:flex;align-items:center;justify-content:center}
.org-node{position:absolute;background:var(--green);color:var(--white);box-shadow:0 4px 8px rgba(0,0,0,.2);padding:8px 10px;font-size:13px;line-height:1.35}
.org-node h5{font-size:14px;font-weight:700;margin-bottom:4px}
.org-node.head{text-align:center;display:flex;align-items:center;justify-content:center;font-weight:700;font-size:14px}
.org-node ul{list-style:none}
.org-node li::before{content:"• "}
.org-node.future{background:var(--white);color:var(--green-dark);border:2px solid var(--green)}

/* footer */
.site-footer{top:3124px;height:440px;background:var(--charcoal)}
.footer-tab{position:absolute;left:465px;top:-40px;width:270px;height:120px;background:var(--charcoal);border-radius:40px 40px 0 0;display:flex;align-items:center;justify-content:center}
.footer-col{position:absolute;top:130px;color:#ddd;font-size:13px}
.footer-col h6{font-family:"Exo 2",sans-serif;font-weight:600;font-size:15px;color:var(--green);text-transform:uppercase;padding-bottom:8px;border-bottom:1px solid #777;margin-bottom:14px;width:190px}
.quick-links-col{left:78px}
.quick-links{list-style:none}
.quick-links li{line-height:1.6;text-transform:uppercase;font-size:12.5px}
.quick-links li::before{content:"› "}
.contact-col{left:335px}
.contact-row{display:flex;gap:10px;margin-bottom:16px;line-height:1.4}
.contact-row svg{flex:none}
.message-col{left:560px}
.message-col h6{width:225px}
.field{width:225px;height:28px;background:#4a4a4a;color:#aaa;font-size:12px;padding:6px 10px;margin-bottom:8px}
.field.tall{height:62px}
.submit{width:100px;height:28px;background:#1b1b1b;color:#fff;font-size:12px;font-weight:700;display:flex;align-items:center;justify-content:center}
.contact-box{position:absolute;left:854px;top:118px;width:282px;height:172px;border:3px solid var(--green);border-radius:6px;text-align:center;color:var(--white);padding-top:22px}
.contact-box h6{font-family:"Exo 2",sans-serif;font-weight:700;font-size:17px;text-transform:uppercase;margin-bottom:10px}
.contact-box .phone{display:flex;align-items:center;justify-content:center;gap:10px;font-family:"Exo 2",sans-serif;font-weight:600;font-size:30px}
.socials{display:flex;justify-content:center;gap:8px;margin-top:14px}
.socials span{width:22px;height:22px;border:2px solid #ddd;border-radius:50%}
.copyright{position:absolute;left:0;bottom:0;width:1200px;height:36px;background:#fff;text-align:center;font-size:10px;line-height:36px;color:#444;letter-spacing:.5px}
</style>
</head>
<body>
<div class="page">

<header class="site-header">
  <div class="hero-visual" role="img" aria-label="Photograph of a space telescope orbiting above the curve of the earth against a black sky"></div>
  <div class="logo-tab"><div class="wordmark">Drabek<br>Partners</div></div>
  <ul class="main-nav">
    <li class="is-active">Home</li>
    <li>Who We Are</li>
    <li>What We Do</li>
    <li>What Makes Us Different</li>
    <li>Our Group</li>
    <li>Contact</li>
  </ul>
  <p class="hero-tagline">people<span class="sep"></span>capital<span class="sep"></span>strategy</p>
</header>

<section class="who">
  <h2 class="section-title"><span class="mark"></span><span>Who <em>We Are</em></span></h2>
  <div class="who-grid">
    <article class="who-card">
      <div class="who-visual v-directors" role="img" aria-label="Illustration of silver figures in an arrow formation led by a blue figure"></div>
      <h3>Leading Directors</h3>
      <p>We identify and connect appropriate resources to the relevant opportunity points to create business momentum.</p>
    </article>
    <article class="who-card">
      <div class="who-visual v-motivators" role="img" aria-label="Illustration of a yellow figure running ahead of a crowd up blue steps"></div>
      <h3>Leading Motivators</h3>
      <p>We generate inspiration, motivation and activation through our shared passion for success and converting opportunity to results.</p>
    </article>
    <article class="who-card">
      <div class="who-visual v-energisers" role="img" aria-label="Photograph of a light bulb sketched in chalk on a green chalkboard"></div>
      <h3>Leading Energisers</h3>
      <p>Together, our collective combination of business capabilities forge a powerful, visible impact – delivered with efficiency and effectiveness.</p>
    </article>
  </div>
  <div class="btn">Learn More</div>
</section>

<section class="do">
  <h2 class="section-title"><span class="mark"></span><span>What <em>We Do</em></span></h2>
  <div class="do-grid">
    <div class="do-col">
      <h3>We Build <em>Ventures</em></h3>
      <ul class="do-list">
        <li>We invest people and financial capital in ventures that have potential.</li>
        <li>We create joint ventures with partners that will bring synergies to our house of brands.</li>
        <li>We confidently venture into new markets, industries and initiatives with entrepreneurial energy.</li>
      </ul>
    </div>
    <div class="do-col">
      <h3>We are <em>Energising Opportunities</em></h3>
      <ul class="do-list">
        <li>Our passion for business, performance and success energises our ventures, our people, and the opportunities we invest in.</li>
        <li>Our vision and focus energises people to see beyond what is, to what could be, opening up new opportunities.</li>
        <li>The opportunities we create energise existing ventures with positive momentum.</li>
      </ul>
    </div>
    <div class="do-col">
      <h3>We Deliver <em>People</em></h3>
      <ul class="do-list">
        <li>We invest in our people supporting their personal and professional growth.</li>
        <li>We invest our people and financial capital into partnerships driving success.</li>
        <li>We provide the strategic leadership, direction and vision with a strategy of empowering our ventures.</li>
      </ul>
    </div>
  </div>
  <div class="btn">Learn More</div>
</section>

<section class="diff">
  <svg class="diff-art" width="1200" height="503" viewBox="0 0 1200 503" aria-hidden="true">
    <g stroke="#fff" stroke-width="2" fill="none" opacity=".85">
      <line x1="440" y1="196" x2="520" y2="232"/>
      <line x1="760" y1="196" x2="680" y2="232"/>
      <line x1="440" y1="356" x2="520" y2="320"/>
      <line x1="760" y1="356" x2="680" y2="320"/>
    </g>
    <g fill="#1c1c1c" stroke="#fff" stroke-width="3">
      <circle cx="410" cy="182" r="38"/>
      <circle cx="790" cy="182" r="38"/>
      <circle cx="410" cy="370" r="38"/>
      <circle cx="790" cy="370" r="38"/>
    </g>
    <g stroke="#fff" stroke-width="3" fill="none" stroke-linecap="round">
      <circle cx="410" cy="182" r="17"/>
      <polyline points="410,171 410,182 418,188"/>
      <rect x="776" y="168" width="20" height="20"/>
      <rect x="784" y="176" width="20" height="20"/>
    </g>
    <g fill="#fff">
      <circle cx="410" cy="360" r="6"/>
      <path d="M398 384a12 12 0 0 1 24 0z"/>
      <circle cx="396" cy="365" r="4.5"/>
      <path d="M387 382a9 9 0 0 1 16-5v5z"/>
      <circle cx="424" cy="365" r="4.5"/>
      <path d="M433 382a9 9 0 0 0-16-5v5z"/>
      <rect x="775" y="376" width="6" height="10"/>
      <rect x="785" y="368" width="6" height="18"/>
      <rect x="795" y="360" width="6" height="26"/>
      <path d="M774 364l14-10 6 4 12-10v4l-12 10-6-4-14 10z"/>
    </g>
  </svg>
  <h2 class="section-title on-green"><span class="mark"></span><span>What Makes Us Different</span></h2>
  <div class="diff-hub"><div class="wordmark">Drabek<br>Partners</div></div>
  <div class="trait left t-responsive"><strong>Responsive</strong> <span class="tag">– Mobile Agility</span><br>We act and respond swiftly –<br>but responsibly</div>
  <div class="trait t-transparent"><strong>Transparent</strong> <span class="tag">– we champion our values</span><br>Connections – leadership – success</div>
  <div class="trait left t-supportive"><strong>Supportive</strong> <span class="tag">– welcoming family</span><br>Considerate and respectful of the<br>importance of lifestyle balance</div>
  <div class="trait t-performance"><strong>Performance</strong> <span class="tag">– network integrity</span><br>Quality, responsibility and consideration</div>
</section>

<section class="group">
  <h2 class="section-title"><span class="mark"></span><span>Our <em>Group</em></span></h2>
  <svg class="org-lines" width="1200" height="760" viewBox="0 0 1200 760" aria-hidden="true">
    <g stroke="#c8c8c8" stroke-width="2" fill="none">
      <line x1="735" y1="184" x2="950" y2="184"/>
      <line x1="604" y1="262" x2="604" y2="297"/>
      <line x1="147" y1="297" x2="1075" y2="297"/>
      <line x1="147" y1="297" x2="147" y2="362"/>
      <line x1="328" y1="297" x2="328" y2="362"/>
      <line x1="514" y1="297" x2="514" y2="362"/>
      <line x1="698" y1="297" x2="698" y2="362"/>
      <line x1="882" y1="297" x2="882" y2="362"/>
      <line x1="1075" y1="297" x2="1075" y2="362"/>
    </g>
  </svg>
  <div class="org-top"><h4>Triveld Energy</h4><p>"Financial &amp; human<br>capital to grow business,<br>people &amp; values"</p></div>
  <div class="org-side">Aviation</div>

  <div class="org-node head" style="left:61px;top:362px;width:172px;height:48px">Harlow Group</div>
  <div class="org-node" style="left:61px;top:423px;width:172px;height:195px">
    <h5>Harlow Group Qld</h5>
    <ul><li>Electrical</li><li>Civil</li><li>Maintenance</li><li>Construction</li><li>Fibre / coms</li><li>Water</li><li>Property M'ment</li><li>Consultation</li></ul>
  </div>
  <div class="org-node" style="left:61px;top:630px;width:172px;height:64px">
    <h5>Harlow Group Vic</h5>
    <ul><li>Electrical</li></ul>
  </div>

  <div class="org-node" style="left:245px;top:362px;width:167px;height:126px">
    <h5 style="text-align:center">Harlow Fuel<br>Solutions</h5>
    <ul><li>Construction</li><li>Service</li><li>Maintenance</li></ul>
  </div>

  <div class="org-node head" style="left:429px;top:362px;width:171px;height:48px">Kestrel Group</div>
  <div class="org-node" style="left:429px;top:423px;width:171px;height:95px">
    <h5>Kestrel Bullbars</h5>
    <ul><li>Bullbars</li><li>Brushrails</li><li>Accessories</li></ul>
  </div>
  <div class="org-node" style="left:429px;top:535px;width:171px;height:107px">
    <h5>Kestrel Coatings</h5>
    <ul><li>Powdercoating</li><li>Spray lining</li><li>Sandblasting</li></ul>
  </div>

  <div class="org-node" style="left:613px;top:362px;width:171px;height:114px">
    <h5 style="text-align:center">Maroda (Aus)</h5>
    <ul><li>Fuel delivery devices for retail fuel industry</li></ul>
  </div>

  <div class="org-node" style="left:796px;top:362px;width:172px;height:126px">
    <h5 style="text-align:center">RVX</h5>
    <ul><li>Rotating Disc Systems</li><li>Water treatment solutions</li></ul>
  </div>

  <div class="org-node head future" style="left:980px;top:362px;width:189px;height:52px">Future Acquisitions...</div>
</section>

<footer class="site-footer">
  <div class="footer-tab"><div class="wordmark">Drabek<br>Partners</div></div>

  <div class="footer-col quick-links-col">
    <h6>Quick Links</h6>
    <ul class="quick-links">
      <li>Home</li><li>Who We Are</li><li>What We Do</li><li>What Makes Us Different</li><li>Our Group</li><li>Contact</li>
    </ul>
  </div>

  <div class="footer-col contact-col">
    <h6>Contact</h6>
    <div class="contact-row">
      <svg width="18" height="18" viewBox="0 0 18 18" aria-hidden="true"><circle cx="9" cy="9" r="8" fill="none" stroke="#ddd" stroke-width="1.5"/><path d="M9 4a3 3 0 0 0-3 3c0 2.3 3 6 3 6s3-3.7 3-6a3 3 0 0 0-3-3z" fill="#ddd"/></svg>
      <span>Drabek Partners<br>123 Lorem Ipsum Dr<br>Sydney</span>
    </div>
    <div class="contact-row">
      <svg width="18" height="18" viewBox="0 0 18 18" aria-hidden="true"><circle cx="9" cy="9" r="8" fill="none" stroke="#ddd" stroke-width="1.5"/><path d="M6 5l2 2-1 1.5c.6 1.3 1.4 2.1 2.5 2.5L11 10l2 2-1.5 1.5C8.5 13 5 9.5 4.5 6.5z" fill="#ddd"/></svg>
      <span>0400 555 218</span>
    </div>
    <div class="contact-row">
      <svg width="18" height="18" viewBox="0 0 18 18" aria-hidden="true"><circle cx="9" cy="9" r="8" fill="none" stroke="#ddd" stroke-width="1.5"/><rect x="5" y="6" width="8" height="6" fill="none" stroke="#ddd" stroke-width="1.3"/><path d="M5 6l4 3 4-3" fill="none" stroke="#ddd" stroke-width="1.3"/></svg>
      <span>info@drabekpartners.com.au</span>
    </div>
  </div>

  <div class="footer-col message-col">
    <h6>Send Us A Message</h6>
    <div class="field">Name</div>
    <div class="field">Email</div>
    <div class="field tall">Message</div>
    <div class="submit">SUBMIT</div>
  </div>

  <div class="contact-box">
    <h6>Contact Us Today</h6>
    <div class="phone">
      <svg width="30" height="30" viewBox="0 0 30 30" aria-hidden="true"><circle cx="15" cy="15" r="13" fill="none" stroke="#fff" stroke-width="2.5"/><path d="M10 8l3.5 3.5-1.8 2.2c1 2 2.4 3.4 4.4 4.4l2.2-1.8L22 20l-2.5 2.5C14 22 8 16 7.5 10.5z" fill="#fff"/></svg>
      <span>0400 555 218</span>
    </div>
    <div class="socials"><span></span><span></span><span></span></div>
  </div>

  <div class="copyright">COPYRIGHT © 2017 DRABEK PARTNERS. ALL RIGHTS RESERVED.</div>
</footer>

</div>
</body>
</html>
```